Insert sheet for our Dog Food Package

We need an information sheet to go inn our pet food package, with branding, and information on ingredients, nutrition and feeding guidance. We will also need two additional items which will be a variation on the label design:
1) Label for package (detailed label about us and our food)
2) Label for outer shipping box (simple label for branding)
We will start with the information, insert page. The winning designer will then deliver the package and box labels as simplified versions of the same graphical theme.
I have attached samples of an earlier drafts of the insert piece. Please disregard the style, form and colors of the examples given. THEY ARE ONLY THERE TO SHOW WHAT INFORMATION SHOULD BE INCLUDED. All colors and style should be from our logo (attached). All graphics, font styles, and placement of elements need to be YOUR creative design - not a copy of the sample we gave. PLEASE READ THIS AND PLEASE DO NOT SUBMIT ANY VARIATION OF THE EXAMPLES!!!!!!!

Target Market(s)

Pet Owners

Industry/Entity Type

Pet Food

Colors
EB3D1F
EC4F4E
F09395
F8D3D4
FCEDEE

Requirements
Must have
• All new design. New colors (based in the palette of our logo), new graphics, new fonts, new placement of elements.
Should not have
• Please disregard the style, form and colors of the examples given. THEY ARE ONLY THERE TO SHOW WHAT INFORMATION SHOULD BE INCLUDED.

```html
<!DOCTYPE html>
<html lang="en">
<head>
<meta charset="utf-8">
<title>Verano – Feeding Insert</title>
<link href="https://fonts.googleapis.com/css2?family=Montserrat:wght@400;500;600;700;800;900&display=swap" rel="stylesheet">
<style>
  :root{
    --red:#a3201a;
    --brown:#4a130b;
    --ink:#151515;
    --grey-bg:#ececec;
    --white:#ffffff;
    --bar-dark:#6b6b6b;
    --bar-light:#d9d9d9;
    --rule:#bdbdbd;
  }
  *{box-sizing:border-box;margin:0;padding:0}
  html,body{width:783px;height:1200px;overflow:hidden;background:#f2f2f2}
  body{font-family:"Montserrat",Arial,sans-serif;color:var(--ink)}
  .sheet{position:relative;width:783px;height:1200px;overflow:hidden;
    background:linear-gradient(180deg,var(--grey-bg) 0%,#f3f3f3 45%,var(--white) 60%,var(--white) 100%)}
  .abs{position:absolute}

  .brand{left:45px;top:60px;display:flex;align-items:center;gap:18px}
  .brand-dot{width:96px;height:96px;border-radius:50%;background:var(--red)}
  .brand-name{font-size:48px;font-weight:600;letter-spacing:5px;color:var(--red);line-height:1}

  .headline{left:48px;top:182px;font-weight:900;line-height:.98;letter-spacing:-1px;text-transform:uppercase}
  .headline .l1{font-size:49px;font-weight:800}
  .headline .l2{font-size:69px}
  .headline .l3{font-size:80px;color:var(--red);margin-top:2px}

  .icons{left:50px;top:418px}

  .dog-photo{left:425px;top:62px;width:358px;height:640px;
    border-radius:46% 46% 8% 8%/30% 30% 4% 4%;
    background:radial-gradient(ellipse at 50% 30%,#c98a4f 0%,#d9b08a 35%,#f1e7dc 60%,rgba(240,240,240,0) 75%)}
  .leash-photo{left:0;top:478px;width:783px;height:220px;
    background:radial-gradient(ellipse 60% 35% at 45% 55%,rgba(40,40,40,.55) 0%,rgba(60,60,60,.25) 50%,rgba(255,255,255,0) 80%)}

  .emblem{left:62px;top:493px;width:156px;height:156px;border-radius:50%;background:var(--red);
    display:flex;align-items:center;justify-content:center;border:8px solid var(--white);box-shadow:0 0 0 3px var(--red)}
  .emblem span{color:var(--white);font-size:24px;font-weight:600;letter-spacing:3px}

  .story-title{left:58px;top:676px;font-size:35px;font-weight:900;color:var(--red);letter-spacing:-.5px}
  .story-lead{left:58px;top:722px;width:660px;font-size:16.5px;font-weight:700;line-height:1.25}
  .quote-mark{left:58px;top:777px}
  .story-body{left:100px;top:782px;width:640px;font-size:12.6px;font-weight:500;line-height:1.33}

  .card{top:856px;background:var(--white);border-radius:16px;overflow:hidden;
    box-shadow:0 2px 8px rgba(0,0,0,.25);z-index:2}
  .card-head{background:var(--brown);color:var(--white);font-size:12.6px;font-weight:700;
    height:45px;display:flex;align-items:center;justify-content:center;letter-spacing:.3px}
  .card-sub{text-align:center;font-size:12.6px;font-weight:600;margin-top:14px;letter-spacing:.2px}
  .nutrition{left:59px;width:308px;height:268px}
  .nutri-grid{display:grid;grid-template-columns:125px 125px;gap:4px 8px;margin:12px 0 0 27px}
  .bar{font-size:12.5px;padding:1px 4px;line-height:16px}
  .bar.dark{background:var(--bar-dark);color:var(--white)}
  .bar.light{background:var(--bar-light);color:#333;padding-left:14px}
  .ingredients{font-size:10.6px;line-height:1.2;margin:16px 16px 0 16px;color:#222}
  .feeding{left:416px;width:321px;height:268px}
  .feed-caption{color:var(--red);font-size:11.6px;font-weight:700;margin:10px 0 0 18px;letter-spacing:.2px}
  .feed-table{margin:4px 30px 0 18px;border-collapse:collapse;width:calc(100% - 48px);font-size:10.6px}
  .feed-table tbody{border-top:1px solid var(--rule)}
  .feed-table tbody td{padding:1px 0;line-height:1.2}
  .feed-table tbody tr:first-child td{padding-top:8px}
  .feed-table tbody tr:last-child td{padding-bottom:5px}
  .feed-table td.grams{text-align:right}
  .feed-table tbody + tbody{border-top:1px solid var(--rule)}

  .footer{left:0;top:1040px;width:783px;height:160px}
  .site{left:0;top:1133px;width:783px;text-align:center;color:var(--white);
    font-size:27px;font-weight:600;letter-spacing:3px}
</style>
</head>
<body>
<main class="sheet">
  <div class="abs dog-photo" role="img" aria-label="Beagle puppy sitting upright"></div>
  <div class="abs leash-photo" role="img" aria-label="Black leather dog leash curving across the page"></div>

  <header class="abs brand">
    <div class="brand-dot"></div>
    <div class="brand-name">VERANO</div>
  </header>

  <h1 class="abs headline">
    <div class="l1">Prepared with</div>
    <div class="l2">Loved for</div>
    <div class="l3">Shadow</div>
  </h1>

  <svg class="abs icons" width="150" height="40" viewBox="0 0 150 40" aria-hidden="true">
    <g fill="#111">
      <ellipse cx="18" cy="26" rx="9" ry="8"/>
      <ellipse cx="6" cy="14" rx="3.5" ry="5"/><ellipse cx="13" cy="7" rx="3.5" ry="5"/>
      <ellipse cx="23" cy="7" rx="3.5" ry="5"/><ellipse cx="30" cy="14" rx="3.5" ry="5"/>
      <ellipse cx="128" cy="26" rx="9" ry="8"/>
      <ellipse cx="116" cy="14" rx="3.5" ry="5"/><ellipse cx="123" cy="7" rx="3.5" ry="5"/>
      <ellipse cx="133" cy="7" rx="3.5" ry="5"/><ellipse cx="140" cy="14" rx="3.5" ry="5"/>
    </g>
    <g fill="#a3201a">
      <rect x="58" y="17" width="34" height="8" rx="2"/>
      <circle cx="57" cy="16" r="5"/><circle cx="57" cy="26" r="5"/>
      <circle cx="93" cy="16" r="5"/><circle cx="93" cy="26" r="5"/>
    </g>
  </svg>

  <div class="abs emblem"><span>VERANO</span></div>

  <h2 class="abs story-title">OUR STORY</h2>
  <p class="abs story-lead">We Revolutionized the industry. Not Formulated to meet a minimum standard, but to develop the maximum health of the whole dog.</p>
  <svg class="abs quote-mark" width="30" height="24" viewBox="0 0 30 24" aria-hidden="true">
    <path fill="#a3201a" d="M0 24V13C0 5 4 1 12 0l1 4c-4 1-6 3-6 7h5v13zM16 24V13c0-8 4-12 12-13l1 4c-4 1-6 3-6 7h5v13z"/>
  </svg>
  <p class="abs story-body">We didn't just set about to create a food that will ‘pass a minimum standard’. We set out to revolutionize the industry by creating a food that is designed with Supertoods, Wholesoe Grains, and Powertul Oils to help your dog achieve their maximu health,happiness andlongevity.</p>

  <svg class="abs footer" width="783" height="160" viewBox="0 0 783 160" aria-hidden="true">
    <path fill="#222" d="M0 0 C15 30 40 50 60 60 L0 60Z"/>
    <path fill="#222" d="M640 25 C700 20 760 30 783 60 L783 80 C760 50 700 40 640 40Z"/>
    <path fill="#a3201a" d="M0 60 L60 60 C300 60 600 50 700 45 C750 42 775 60 783 75 L783 160 L0 160Z"/>
  </svg>

  <section class="abs card nutrition">
    <div class="card-head">WE PREPARED THE BEST TOR SHADOW</div>
    <div class="card-sub">NUTRITIONAL INFORMATION</div>
    <div class="nutri-grid">
      <div class="bar dark">Protein: 15%</div><div class="bar light">Total Fat: 9.5%</div>
      <div class="bar dark">Crude Fiber: 2.0%</div><div class="bar light">Moisture: 72%</div>
    </div>
    <p class="ingredients">Potassium Citrate, DiCalcium Phosphate, Calcium Carbonate, Garbanzo Beans, Choline Bitartrate, Taurine, Salt, Zinc Proteinate, Magnesium Oxide, Iron Proteinate, Vitamin B-12, Selenium, Niacin, Riboflavin, Calcium Panthothen-ate, Thimine, Vitamin A, Vitamin D, Calcium Iodate, Vitamin B6, Folic Acid</p>
  </section>

  <section class="abs card feeding">
    <div class="card-head">HOW MUCH SHOULD I FEED SHADOW?</div>
    <div class="card-sub">RECOMMENDED FEEDING PLAN</div>
    <div class="feed-caption">APPROXIMATE WEIGHT FULL MEAL</div>
    <table class="feed-table">
      <tbody><tr><td>&lt;20 lbs</td><td class="grams">110 g</td></tr></tbody>
      <tbody>
        <tr><td>20-29 lbs</td><td class="grams">200 g</td></tr>
        <tr><td>30-39 lbs</td><td class="grams">250 g</td></tr>
        <tr><td>40-54 lbs</td><td class="grams">300 g</td></tr>
      </tbody>
      <tbody>
        <tr><td>55-69 lbs</td><td class="grams">350 g</td></tr>
        <tr><td>70-85 lbs</td><td class="grams">400 g</td></tr>
      </tbody>
      <tbody><tr><td>85+ lbs</td><td class="grams">500 g</td></tr></tbody>
    </table>
  </section>

  <footer class="abs site">www.veranodog.com</footer>
</main>
</body>
</html>
```